Advertisement Design

I'm looking for a post card sized advertisement piece that I will be dropping off to commercial and residential customers.
On one side I want it promoting carpet cleaning services and on the other side dryer vent cleaning services.
I've uploaded two different layouts of my company logo for you to choice from.
One batch will be printed with my Michigan Number
One batch will be printed with my Tennessee number
Will share contact numbers with the winner so just use a make up number
742-318-9516

```html
<!DOCTYPE html>
<html lang="en">
<head>
<meta charset="utf-8">
<title>Nap Nomad Postcards</title>
<link href="https://fonts.googleapis.com/css2?family=Cinzel:wght@500;700&family=Poppins:wght@400;500;600;700&display=swap" rel="stylesheet">
<style>
:root{
  --blue:#1178c0;
  --blue-bright:#2a95e0;
  --ink:#3a3a3a;
  --band:#4b4d52;
  --band-dark:#3c3e42;
  --paper:#f3f3f3;
  --stage:#a3a3a3;
  --white:#ffffff;
}
*{margin:0;padding:0;box-sizing:border-box}
html,body{width:872px;height:1200px;overflow:hidden;background:var(--stage)}
body{position:relative;font-family:'Poppins',sans-serif;color:var(--ink)}
.card{position:absolute;left:94px;width:684px;height:456px;background:var(--paper);overflow:hidden}
.card--carpet{top:112px;background:linear-gradient(135deg,#f6f6f6,#e9e9e9)}
.card--dryer{top:632px;background:linear-gradient(160deg,#fafafa,#ececec)}
.brand{position:absolute;display:flex;align-items:center;gap:10px}
.brand__mark{width:34px;height:34px;background:var(--blue);border-radius:4px}
.brand__rule{width:2px;height:60px;background:var(--ink)}
.brand__name{font-family:'Cinzel',serif;font-weight:500;font-size:19px;color:var(--blue);letter-spacing:.5px;line-height:1}
.brand__sub{font-family:'Cinzel',serif;font-size:5.5px;letter-spacing:1.6px;color:var(--ink);border-top:1px solid var(--ink);margin-top:3px;padding-top:2px;text-align:center}
.kicker{position:absolute;left:32px;font-family:'Cinzel',serif;font-weight:500;color:var(--ink);line-height:1}
.headline{position:absolute;left:32px;font-family:'Cinzel',serif;font-weight:700;color:var(--blue);line-height:.95}
.intro{position:absolute;left:32px;top:222px;width:372px;font-size:10.6px;line-height:1.2;color:#222}
.services{position:absolute;left:0;top:298px;width:684px;height:87px;background:var(--band)}
.service{position:absolute;top:-14px;width:62px;margin-left:-31px;text-align:center;color:var(--white);font-size:9.3px;line-height:1.22}
.service--wide{width:70px;margin-left:-35px}
.service__icon{display:block;width:38px;height:38px;margin:0 auto 6px;border-radius:50%;background:var(--blue);border:2px solid var(--white)}
.service__sep{position:absolute;top:8px;width:1px;height:62px;background:#777}
.photo-circle{position:absolute;left:400px;top:-40px}
.contact{position:absolute;left:32px;width:652px;height:36px}
.contact__lead{position:absolute;left:0;top:0;font-family:'Cinzel',serif;font-weight:700;font-size:17px;line-height:.95}
.contact__lead span{display:block;color:var(--ink);font-weight:500}
.contact__lead b{color:var(--blue);font-weight:700}
.contact__item{position:absolute;top:9px;display:flex;align-items:center;gap:4px;font-size:14.5px;font-weight:500;color:var(--ink);white-space:nowrap}
.contact__item--email{font-size:13.6px;letter-spacing:-.3px}
.contact__icon{width:15px;height:15px;flex:none}
.url-bar{position:absolute;left:427px;top:9px;width:225px;height:21px;background:var(--blue);border-radius:11px 0 0 11px;color:var(--white);font-size:13px;letter-spacing:2.4px;line-height:21px;padding-left:16px;box-shadow:0 3px 4px rgba(0,0,0,.25)}
.url-bar b{font-weight:700}
.steps{position:absolute;left:0;top:134px;width:684px;height:141px;background:linear-gradient(90deg,var(--band-dark),var(--band) 60%,#5a5c61)}
.steps__title{position:absolute;left:31px;top:6px;font-weight:700;font-size:15.5px;color:var(--white);letter-spacing:-.2px}
.steps__title em{font-style:normal;color:var(--blue-bright)}
.steps__divider{position:absolute;left:326px;top:30px;width:1px;height:108px;background:#8a8a8a}
.step{position:absolute;display:flex;align-items:center;gap:7px;color:var(--white)}
.step__icon{width:28px;height:28px;border-radius:50%;background:var(--blue);border:2px solid var(--white);flex:none}
.step__label{font-weight:700;font-size:11px;color:var(--blue-bright);line-height:1}
.step__text{font-size:11.5px;line-height:1.2}
.gallery__photo{position:absolute;top:284px;width:132px;height:100px;border:2px solid var(--blue)}
.note{position:absolute;left:462px;top:281px;width:194px;font-size:9.4px;line-height:1.22;color:#222}
</style>
</head>
<body>

<section class="card card--carpet">
  <svg class="photo-circle" width="340" height="470" viewBox="0 0 340 470">
    <circle cx="184" cy="178" r="180" fill="#5b5c60"/>
    <circle cx="196" cy="178" r="172" fill="#f2f2f2"/>
    <g role="img" aria-label="Technician vacuuming a blue office corridor carpet">
      <circle cx="204" cy="178" r="168" fill="#0f68ad"/>
    </g>
  </svg>

  <div class="brand" style="left:32px;top:28px">
    <div class="brand__mark"></div>
    <div class="brand__rule"></div>
    <div>
      <div class="brand__name">NAP NOMAD</div>
      <div class="brand__sub">PROPERTY SERVICES</div>
    </div>
  </div>

  <div class="kicker" style="top:96px;font-size:27px">NAP NOMAD</div>
  <div class="headline" style="top:122px;font-size:54px">CARPET</div>
  <div class="headline" style="top:172px;font-size:54px">CLEANING</div>

  <p class="intro">We have been providing Carpet Cleaning Services for 40 years. With state-of-the-art industrial equipment &amp; our years of experience there is not much we cannot get clean. Carpet Cleaning Services include the following.</p>

  <div class="services">
    <div class="service" style="left:52px"><span class="service__icon"></span>Industrial Carpet Cleaning</div>
    <div class="service__sep" style="left:84px"></div>
    <div class="service service--wide" style="left:118px"><span class="service__icon"></span>Residential Carpet Cleaning</div>
    <div class="service__sep" style="left:152px"></div>
    <div class="service" style="left:180px;width:50px;margin-left:-25px"><span class="service__icon"></span>Rug Cleaning</div>
    <div class="service__sep" style="left:209px"></div>
    <div class="service service--wide" style="left:247px"><span class="service__icon"></span>Boat, RV, Private Plane Carpet Cleaning</div>
    <div class="service__sep" style="left:286px"></div>
    <div class="service service--wide" style="left:322px"><span class="service__icon"></span>Tile &amp; Grout steam cleaning / sealing</div>
    <div class="service__sep" style="left:363px"></div>
    <div class="service" style="left:395px"><span class="service__icon"></span>Corridor &amp; Outdoor Carpet Cleaning</div>
  </div>

  <div class="contact" style="top:393px">
    <div class="contact__lead"><b>CONTACT</b><span>US TODAY</span></div>
    <div class="contact__item" style="left:103px">
      <svg class="contact__icon" viewBox="0 0 16 16"><circle cx="8" cy="8" r="8" fill="var(--blue)"/><path d="M5 4.5l1.6-.3.8 2-1 .8a6 6 0 0 0 2.6 2.6l.8-1 2 .8-.3 1.6c-3.7.3-6.8-2.8-6.5-6.5z" fill="#fff"/></svg>742-318-9516</div>
    <div class="contact__item contact__item--email" style="left:237px">
      <svg class="contact__icon" viewBox="0 0 16 16"><circle cx="8" cy="8" r="8" fill="var(--blue)"/><rect x="4" y="5.2" width="8" height="5.6" rx=".6" fill="#fff"/><path d="M4.3 5.6L8 8.4l3.7-2.8" stroke="var(--blue)" stroke-width=".9" fill="none"/></svg>Billing@napnomad.com</div>
    <div class="url-bar">www.<b>napnomad</b>.com</div>
  </div>
</section>

<section class="card card--dryer">
  <div class="kicker" style="top:30px;font-size:25px">NAP NOMAD</div>
  <div class="headline" style="top:57px;font-size:38px">DRYER VENT</div>
  <div class="headline" style="top:92px;font-size:38px">CLEANING</div>

  <div class="brand" style="left:430px;top:33px">
    <div class="brand__mark" style="width:44px;height:44px"></div>
    <div class="brand__rule" style="height:78px"></div>
    <div>
      <div class="brand__name" style="font-size:24px">NAP NOMAD</div>
      <div class="brand__sub" style="font-size:6.5px">PROPERTY SERVICES</div>
    </div>
  </div>

  <div class="steps">
    <div class="steps__title">HOW DO YOU <em>CLEAN A DRYER VENT?</em></div>
    <div class="steps__divider"></div>
    <div class="step" style="left:31px;top:35px"><span class="step__icon"></span><div><div class="step__label">STEP 1</div><div class="step__text">Gather your supplies</div></div></div>
    <div class="step" style="left:31px;top:71px"><span class="step__icon"></span><div><div class="step__label">STEP 2</div><div class="step__text">Disconnect the duct</div></div></div>
    <div class="step" style="left:31px;top:107px"><span class="step__icon"></span><div><div class="step__label">STEP 3</div><div class="step__text">Vacuum the entrance to the dryer vent</div></div></div>
    <div class="step" style="left:346px;top:35px"><span class="step__icon"></span><div><div class="step__label">STEP 4</div><div class="step__text">Connect the rods in a dryer duct cleaning kit</div></div></div>
    <div class="step" style="left:346px;top:71px"><span class="step__icon"></span><div><div class="step__label">STEP 5</div><div class="step__text">Turn on the drill</div></div></div>
    <div class="step" style="left:346px;top:107px"><span class="step__icon"></span><div><div class="step__label">STEP 6</div><div class="step__text">Clean up the mess inside</div></div></div>
  </div>

  <div class="gallery__photo" role="img" aria-label="Technician inspecting a duct fitting" style="left:33px;background:linear-gradient(135deg,#d9dde2,#8e99a6)"></div>
  <div class="gallery__photo" role="img" aria-label="Metal ventilation ducts on a ceiling" style="left:173px;background:linear-gradient(135deg,#aeb3b8,#6c737a)"></div>
  <div class="gallery__photo" role="img" aria-label="Technician on a ladder servicing a vent unit" style="left:312px;background:linear-gradient(135deg,#c9b58f,#8a7352)"></div>

  <p class="note">While the standard advice is to whip out your vent brush about once every 12 months to make sure your dryer vent duct is free of lint and other debris, you may need to put your dryer vent cleaning kit to use more often if your household has pets or if you have a large family or lots of laundry (think kids who play a ton of sports).</p>

  <div class="contact" style="top:393px">
    <div class="contact__lead"><b>CONTACT</b><span>US TODAY</span></div>
    <div class="contact__item" style="left:103px">
      <svg class="contact__icon" viewBox="0 0 16 16"><circle cx="8" cy="8" r="8" fill="var(--blue)"/><path d="M5 4.5l1.6-.3.8 2-1 .8a6 6 0 0 0 2.6 2.6l.8-1 2 .8-.3 1.6c-3.7.3-6.8-2.8-6.5-6.5z" fill="#fff"/></svg>742-318-9516</div>
    <div class="contact__item contact__item--email" style="left:237px">
      <svg class="contact__icon" viewBox="0 0 16 16"><circle cx="8" cy="8" r="8" fill="var(--blue)"/><rect x="4" y="5.2" width="8" height="5.6" rx=".6" fill="#fff"/><path d="M4.3 5.6L8 8.4l3.7-2.8" stroke="var(--blue)" stroke-width=".9" fill="none"/></svg>Billing@napnomad.com</div>
    <div class="url-bar">www.<b>napnomad</b>.com</div>
  </div>
</section>

</body>
</html>
```